K7 Electrical Services Ltd Web design

I require a web site for my new electrical contracting company. We are customer service orientated. Offering high value electrical installations, design and maintenance. Focused on custom residential and commercial upgrading. Lighting design and application are paramount in our company's services. Industry leading product use and integration are always on the forefront with our customer client services. As well as energy efficiency.

Target Market(s)

Homebuilders, General Contractors, Property management companies, clients, individuals,

Industry/Entity Type

Electric Company

Coding

Coded - Design and coding required

Number of Pages Required

3 page

Requirements
Must have
• Classic, modern, edgy but not trendy . Appeals to the masse.
• 3 page
• home page
• about page
• gallery page
• ability to contact from the webiste
Nice to have
• open to all types of designs that are relative to the construction industry.
• Black, Grey, metallic ice blue and deep purple colours from the logo.
Should not have
• anything cheesy with cartoon light bulb images.

```html
<!DOCTYPE html>
<html lang="en">
<head>
<meta charset="utf-8">
<title>K7 Electrical Services Ltd</title>
<link href="https://fonts.googleapis.com/css2?family=Lato:wght@400;700;900&family=Open+Sans:ital,wght@0,400;0,600;0,700;1,400&display=swap" rel="stylesheet">
<style>
:root{
  --purple:#5a2d8c;
  --purple-dark:#4a2275;
  --purple-soft:#7b52a8;
  --ink:#1e1e1e;
  --text:#6f6f6f;
  --muted:#9a9a9a;
  --line:#e3e3e3;
  --grey-bg:#f4f4f4;
  --footer:#2a2828;
  --white:#ffffff;
}
*{box-sizing:border-box;margin:0;padding:0}
html,body{width:1200px;height:3854px;overflow:hidden}
body{font-family:"Open Sans",Arial,sans-serif;color:var(--text);background:var(--white);position:relative}
h1,h2,h3,h4{font-family:"Lato",Arial,sans-serif;color:var(--ink)}
.abs{position:absolute}
.photo{position:absolute}
.btn{display:inline-flex;align-items:center;gap:8px;border-radius:22px;font-family:"Lato",Arial,sans-serif;font-weight:700;font-size:14px;letter-spacing:.5px;text-transform:uppercase}
.btn .dot{width:14px;height:14px;border-radius:50%;display:inline-flex;align-items:center;justify-content:center}

/* header */
.site-header{position:absolute;top:0;left:0;width:1200px;height:116px;background:var(--white)}
.brand{position:absolute;left:97px;top:34px;display:flex;align-items:center;gap:10px}
.brand-mark{width:18px;height:18px;background:var(--purple);border-radius:2px}
.brand-name{font-family:"Lato",Arial,sans-serif;font-weight:700;font-size:20px;color:var(--purple);line-height:1}
.top-contact{position:absolute;right:97px;top:28px;display:flex;gap:28px;font-size:13px;color:#555;align-items:center}
.top-contact span{display:flex;align-items:center;gap:8px}
.top-contact .sep{width:1px;height:18px;background:#ccc}
.main-nav{position:absolute;right:97px;top:70px;display:flex;gap:30px;font-family:"Lato",Arial,sans-serif;font-weight:700;font-size:14px;color:#333;align-items:center}
.main-nav .active{color:var(--purple)}

/* hero */
.hero{position:absolute;top:116px;left:0;width:1200px;height:544px;background:linear-gradient(90deg,#f3f2f4 0%,#eceaee 45%,#d9d4d2 70%,#b9a49a 100%)}
.hero-title{position:absolute;left:97px;top:150px;font-size:54px;font-weight:900;color:var(--purple);letter-spacing:.5px}
.hero-text{position:absolute;left:97px;top:230px;width:420px;font-size:17px;font-weight:600;color:var(--purple);line-height:1.5}
.hero .btn{position:absolute;left:97px;top:338px;background:var(--purple);color:#fff;padding:12px 26px;height:46px}
.hero .btn .dot{background:#fff;color:var(--purple)}
.slider-arrow{position:absolute;width:36px;height:36px;border-radius:50%;background:rgba(120,120,120,.45);display:flex;align-items:center;justify-content:center}

/* feature cards */
.feature-card{position:absolute;top:748px;width:318px;height:212px}
.feature-card.commercial{background:var(--purple);text-align:center;color:#fff}
.feature-card.commercial h3{color:#fff;font-size:21px;margin-top:62px;font-weight:700}
.feature-card.commercial p{font-size:12px;line-height:1.5;margin:10px auto 0;width:220px;color:#e8dff2}
.feature-card.commercial .btn{position:absolute;left:87px;bottom:-14px;background:#fff;color:var(--purple);border:1px solid var(--purple);padding:8px 20px;font-size:12px}
.feature-card .btn .dot{background:var(--purple);color:#fff}

/* welcome */
.welcome{position:absolute;top:1070px;left:0;width:1200px;height:468px;background:var(--grey-bg)}
.welcome h2{position:absolute;left:97px;top:80px;font-size:34px;font-weight:900}
.welcome .copy{position:absolute;left:97px;top:142px;width:480px;font-size:13px;line-height:1.75;color:var(--muted)}
.welcome .copy p+p{margin-top:18px}
.welcome .btn{position:absolute;left:97px;top:342px;border:2px solid var(--purple);color:var(--purple);padding:8px 22px;font-size:13px}
.welcome .btn .dot{background:var(--purple);color:#fff}
.video{position:absolute;left:637px;top:82px;width:465px;height:305px;background:linear-gradient(120deg,#5b6670,#9aa4ab 45%,#e5e6e8 70%,#c9ced4);border:6px solid #fff;box-shadow:0 2px 6px rgba(0,0,0,.12)}
.play{position:absolute;left:185px;top:116px;width:62px;height:62px;border-radius:50%;background:#d8242c;display:flex;align-items:center;justify-content:center}

/* services */
.section-title{position:absolute;left:0;width:1200px;text-align:center;font-size:32px;font-weight:900}
.service-card{position:absolute;top:1735px;width:318px;height:198px;border:1px solid var(--line);background:#fff;text-align:center}
.service-icon{position:absolute;top:-44px;left:124px;width:70px;height:70px;border-radius:50%;background:#fff;border:1px solid var(--line);display:flex;align-items:center;justify-content:center}
.service-card h3{font-size:16px;font-weight:700;margin-top:62px;text-transform:uppercase;color:#333}
.service-card p{font-size:12.5px;line-height:1.65;width:250px;margin:12px auto 0;color:var(--muted)}
.service-card a{display:block;margin-top:14px;font-family:"Lato",Arial,sans-serif;font-weight:700;font-size:13px;color:var(--purple);text-decoration:none}

/* testimonials */
.testimonials{position:absolute;top:2023px;left:0;width:1200px;height:387px;background:linear-gradient(90deg,#6a3a9c,#7a4cab 50%,#6b3c9d)}
.testimonials .section-title{color:#fff;top:70px}
.quote{position:absolute;top:170px;width:470px;display:flex;gap:24px}
.avatar{flex:none;width:124px;height:124px;border-radius:50%;border:5px solid #fff;background:linear-gradient(#cfc3d9,#8e78a6);position:relative}
.avatar .mark{position:absolute;left:40px;bottom:-18px;width:34px;height:34px;border-radius:50%;background:#fff;display:flex;align-items:center;justify-content:center;color:var(--purple);font-family:"Lato",Arial,sans-serif;font-weight:900;font-size:22px}
.quote p{font-size:13px;font-style:italic;color:#fff;line-height:1.65;font-weight:600;margin-top:10px}
.quote .who{margin-top:16px;font-style:normal;font-size:14px;font-weight:700;color:#fff}
.quote .who span{font-weight:400;font-size:12px}

/* projects */
.projects-intro{position:absolute;top:2558px;left:300px;width:600px;text-align:center;font-size:13px;line-height:1.7;color:var(--muted)}
.project{position:absolute}
.project-feature{background:linear-gradient(160deg,#6b4a8c,#4e2f70);text-align:center;color:#fff}
.project-feature .panel{position:absolute;left:22px;top:22px;right:22px;bottom:22px;background:rgba(90,45,140,.75)}
.project-feature .tag{margin-top:104px;font-family:"Lato",Arial,sans-serif;font-weight:700;font-size:15px;color:#fff}
.project-feature h3{color:#fff;font-size:24px;font-weight:700;margin-top:10px}
.project-feature p{font-size:12.5px;line-height:1.6;width:240px;margin:12px auto 0;color:#ece4f5}
.project-feature a{display:inline-block;margin-top:16px;font-family:"Lato",Arial,sans-serif;font-weight:700;font-size:13px;color:#fff;border-bottom:1px solid #fff;text-decoration:none}

/* partners */
.partners{position:absolute;top:3128px;left:0;width:1200px;height:222px;background:#f0f0f0}
.partner{position:absolute;top:67px;width:188px;height:84px;background:#fff;border-bottom:4px solid var(--purple);display:flex;align-items:center;justify-content:center}
.partner i{display:block;width:120px;height:26px;background:#d9d9d9;border-radius:3px}

/* footer */
.site-footer{position:absolute;top:3350px;left:0;width:1200px;height:427px;background:var(--footer);color:#cfcfcf}
.pillar{position:absolute;top:78px;display:flex;gap:20px;width:330px}
.pillar .badge{flex:none;width:90px;height:90px;border-radius:50%;background:var(--purple);display:flex;align-items:center;justify-content:center}
.pillar h4{color:#fff;font-size:17px;font-weight:700;margin-top:12px}
.pillar p{font-size:11.5px;line-height:1.6;margin-top:8px;color:#bdbdbd}
.footer-brand{position:absolute;left:450px;top:112px;width:300px;text-align:center;font-family:"Lato",Arial,sans-serif;font-weight:700;font-size:20px;color:#fff;line-height:1.2}
.footer-col{position:absolute;top:280px;font-size:12.5px}
.footer-col h4{color:#fff;font-size:14px;font-weight:700;text-transform:uppercase;margin-bottom:18px}
.footer-col li{list-style:none;display:flex;align-items:center;gap:10px;margin-bottom:10px}
.footer-col li::before{content:"";border-left:6px solid #ccc;border-top:4px solid transparent;border-bottom:4px solid transparent}
.footer-col.contact li::before{display:none}
.social{display:flex;gap:10px}
.social i{width:28px;height:28px;border:1.5px solid #ddd;border-radius:50%;display:block}
.copyright{position:absolute;top:3777px;left:0;width:1200px;height:77px;background:var(--purple);color:#efe7f7;font-size:12.5px;display:flex;align-items:center;justify-content:center}
</style>
</head>
<body>

<header class="site-header">
  <div class="brand"><span class="brand-mark"></span><div class="brand-name">K7 Electrical Services Ltd</div></div>
  <div class="top-contact">
    <span><svg width="13" height="13" viewBox="0 0 24 24"><path fill="#777" d="M6.6 10.8a15 15 0 006.6 6.6l2.2-2.2c.3-.3.7-.4 1-.2 1.1.4 2.3.6 3.6.6.6 0 1 .4 1 1V20c0 .6-.4 1-1 1C10.6 21 3 13.4 3 4c0-.6.4-1 1-1h3.5c.6 0 1 .4 1 1 0 1.3.2 2.5.6 3.6.1.3 0 .7-.2 1z"/></svg>(+1) 555 010 4782</span>
    <span class="sep"></span>
    <span><svg width="14" height="11" viewBox="0 0 24 18"><rect width="24" height="18" rx="2" fill="#777"/><path d="M2 2l10 8 10-8" stroke="#fff" stroke-width="2" fill="none"/></svg>info@k7electrical.com</span>
  </div>
  <nav class="main-nav">
    <span class="active">HOME</span><span>ABOUT</span><span>OUR SERVICES</span><span>PROJECTS</span><span>BLOG</span><span>CONTACT</span>
    <svg width="14" height="14" viewBox="0 0 24 24"><circle cx="10" cy="10" r="7" stroke="#333" stroke-width="3" fill="none"/><path d="M15 15l7 7" stroke="#333" stroke-width="3"/></svg>
  </nav>
</header>

<section class="hero">
  <div class="photo" role="img" aria-label="Electrician fitting a ceiling light fixture" style="left:600px;top:0;width:600px;height:544px;background:linear-gradient(100deg,rgba(236,234,238,0) 0%,rgba(200,180,170,.35) 50%,rgba(150,120,110,.4) 100%)"></div>
  <h1 class="hero-title">K7 ELECTRICAL</h1>
  <p class="hero-text">Nemo enim ipsam voluptatem quia voluptasaut odit sit aspernatur aut odit fugit, sed quia</p>
  <span class="btn">Read more <span class="dot"><svg width="8" height="8" viewBox="0 0 8 8"><path d="M2 1l3 3-3 3" stroke="currentColor" stroke-width="1.6" fill="none"/></svg></span></span>
  <div class="slider-arrow" style="left:24px;top:258px"><svg width="12" height="12" viewBox="0 0 12 12"><path d="M8 1L3 6l5 5" stroke="#fff" stroke-width="2" fill="none"/></svg></div>
  <div class="slider-arrow" style="right:24px;top:258px"><svg width="12" height="12" viewBox="0 0 12 12"><path d="M4 1l5 5-5 5" stroke="#fff" stroke-width="2" fill="none"/></svg></div>
</section>

<div class="feature-card photo" role="img" aria-label="Modern house at dusk with lit garden deck" style="left:97px;background:linear-gradient(160deg,#8a9aa0,#4b4a3e 60%,#a07a4a)"></div>
<div class="feature-card commercial" style="left:441px">
  <h3>COMMERCIAL</h3>
  <p>Nemo enim ipsam voluptatem quia voluptas sit aspernatur aut odit aut fugit sed</p>
  <span class="btn">Read more <span class="dot"><svg width="8" height="8" viewBox="0 0 8 8"><path d="M2 1l3 3-3 3" stroke="#fff" stroke-width="1.6" fill="none"/></svg></span></span>
</div>
<div class="feature-card photo" role="img" aria-label="Two electricians working at a switchboard" style="left:784px;background:linear-gradient(150deg,#d8d6d0,#8d9178 50%,#3f4a35)"></div>

<section class="welcome">
  <h2>WELCOME TO K7 ELECTRICAL</h2>
  <div class="copy">
    <p>We deliver careful electrical work for homes and businesses, with clear quotes, tidy sites and a finish built to last.</p>
    <p>From lighting design to full panel upgrades, our licensed team plans each job around your space, your schedule and your budget. We use proven products, test every circuit and leave you with work that saves energy year after year.</p>
  </div>
  <span class="btn">Read more <span class="dot"><svg width="8" height="8" viewBox="0 0 8 8"><path d="M2 1l3 3-3 3" stroke="#fff" stroke-width="1.6" fill="none"/></svg></span></span>
  <div class="video" role="img" aria-label="Video still of an electrician checking a control cabinet">
    <div class="play"><svg width="22" height="24" viewBox="0 0 22 24"><path d="M3 2l17 10L3 22z" fill="#fff"/></svg></div>
  </div>
</section>

<h2 class="section-title" style="top:1615px">OUR SERVICES</h2>
<div class="service-card" style="left:97px">
  <div class="service-icon"><svg width="40" height="40" viewBox="0 0 40 40"><path d="M8 32L28 12M12 8l20 20" stroke="var(--purple)" stroke-width="5" stroke-linecap="round"/><circle cx="29" cy="10" r="5" fill="none" stroke="var(--purple)" stroke-width="3"/></svg></div>
  <h3>Install &amp; Upgrades</h3>
  <p>At vero eos srarct accusamus et iusto odio dignissimos ducimus qui blanditiis</p>
  <a>READ MORE ➔</a>
</div>
<div class="service-card" style="left:441px">
  <div class="service-icon"><svg width="40" height="40" viewBox="0 0 40 40"><circle cx="20" cy="13" r="7" fill="var(--purple)"/><path d="M7 36c0-8 6-13 13-13s13 5 13 13z" fill="var(--purple)"/><path d="M28 6l5 5-8 8" stroke="var(--purple)" stroke-width="3" fill="none"/></svg></div>
  <h3>Design &amp; Repair</h3>
  <p>At vero eos srarct accusamus et iusto odio dignissimos ducimus qui blanditiis</p>
  <a>READ MORE ➔</a>
</div>
<div class="service-card" style="left:784px">
  <div class="service-icon"><svg width="40" height="40" viewBox="0 0 40 40"><rect x="12" y="12" width="16" height="12" rx="3" transform="rotate(-45 20 18)" fill="var(--purple)"/><path d="M27 11l6-6M8 32l6-6" stroke="var(--purple)" stroke-width="3" stroke-linecap="round"/></svg></div>
  <h3>Electrical Maintenance</h3>
  <p>At vero eos srarct accusamus et iusto odio dignissimos ducimus qui blanditiis</p>
  <a>READ MORE ➔</a>
</div>

<section class="testimonials">
  <h2 class="section-title">WHAT OUR CLIENTS SAY</h2>
  <div class="quote" style="left:97px">
    <div class="avatar" role="img" aria-label="Client portrait"><span class="mark">“</span></div>
    <div><p>“ Magni dolores eos qui ratne voluptem sequi nesciunt Nam libero tempore, cum soluta nobis est eligendi quod maxime placeat facere possimus ”</p><div class="who">ANITA VALE, <span>Harbor Realty.</span></div></div>
  </div>
  <div class="quote" style="left:640px">
    <div class="avatar" role="img" aria-label="Client portrait"><span class="mark">“</span></div>
    <div><p>“ Magni dolores eos qui ratne voluptem sequi nesciunt Nam libero tempore, cum soluta nobis est eligendi quod maxime placeat facere possimus ”</p><div class="who">MARK DALEN, <span>Site Coordinator.</span></div></div>
  </div>
  <div class="slider-arrow" style="left:10px;top:175px;width:28px;height:28px;background:rgba(0,0,0,.25)"><svg width="10" height="10" viewBox="0 0 12 12"><path d="M8 1L3 6l5 5" stroke="#fff" stroke-width="2" fill="none"/></svg></div>
  <div class="slider-arrow" style="right:10px;top:175px;width:28px;height:28px;background:rgba(0,0,0,.25)"><svg width="10" height="10" viewBox="0 0 12 12"><path d="M4 1l5 5-5 5" stroke="#fff" stroke-width="2" fill="none"/></svg></div>
</section>

<h2 class="section-title" style="top:2490px">LATEST PROJECTS</h2>
<p class="projects-intro">On the other hand, we denounce with righteous indignation and dislike men who are so beguiled and demoralized by the charms of pleasure of the moment,</p>

<div class="project project-feature" role="img" aria-label="Project photo of a lighting installation" style="left:97px;top:2653px;width:356px;height:385px">
  <div class="panel">
    <div class="tag">K7 Electrical Services Ltd</div>
    <h3>Project Name</h3>
    <p>At vero eos et accusamus et iusto odio dignissimos ducimus qui blanditiis</p>
    <a>VIEW ➔</a>
  </div>
</div>
<div class="project" role="img" aria-label="Electrician in hard hat with cable reels" style="left:467px;top:2653px;width:305px;height:177px;background:linear-gradient(140deg,#d9c84a,#8aa0b8 55%,#4b5c72)"></div>
<div class="project" role="img" aria-label="Multimeter testing a breaker panel" style="left:795px;top:2653px;width:305px;height:177px;background:linear-gradient(140deg,#3e4550,#9aa0a8 55%,#c2873a)"></div>
<div class="project" role="img" aria-label="Cables, pliers and electrical tools" style="left:467px;top:2856px;width:305px;height:182px;background:linear-gradient(140deg,#d7d2c8,#9b8d7c 55%,#c04a3a)"></div>
<div class="project" role="img" aria-label="Ceiling with recessed lights and air unit" style="left:795px;top:2856px;width:305px;height:182px;background:linear-gradient(140deg,#f2efe8,#d8cdb8 55%,#b9aa92)"></div>

<section class="partners">
  <svg class="abs" style="left:40px;top:100px" width="12" height="20" viewBox="0 0 12 20"><path d="M10 2L2 10l8 8" stroke="#aaa" stroke-width="2" fill="none"/></svg>
  <div class="partner" style="left:97px"><i></i></div>
  <div class="partner" style="left:300px"><i></i></div>
  <div class="partner" style="left:505px"><i></i></div>
  <div class="partner" style="left:708px"><i></i></div>
  <div class="partner" style="left:912px"><i></i></div>
  <svg class="abs" style="right:40px;top:100px" width="12" height="20" viewBox="0 0 12 20"><path d="M2 2l8 8-8 8" stroke="#aaa" stroke-width="2" fill="none"/></svg>
</section>

<footer class="site-footer">
  <div class="pillar" style="left:97px">
    <div class="badge"><svg width="44" height="44" viewBox="0 0 40 40"><path d="M8 32L28 12M12 8l20 20" stroke="#fff" stroke-width="5" stroke-linecap="round"/></svg></div>
    <div><h4>Industry Leading Product</h4><p>Nam libero tempore, cum soluta nobis est eligendi optio cumque nihil</p></div>
  </div>
  <div class="footer-brand">K7 Electrical Services Ltd</div>
  <div class="pillar" style="left:768px">
    <div class="badge"><svg width="40" height="40" viewBox="0 0 40 40"><path d="M6 18h7v16H6zM15 18l7-12c3 0 4 2 3 6l-1 4h9c2 0 3 2 2 4l-4 12c-1 2-2 2-4 2H15z" fill="#fff"/></svg></div>
    <div><h4>Industry Integration</h4><p>Nam libero tempore, cum soluta nobis est eligendi optio cumque nihil</p></div>
  </div>
  <div class="footer-col contact" style="left:97px">
    <h4>Contact Us</h4>
    <ul><li>☏&nbsp; (+1) 555 010 4782</li><li>✉&nbsp; info@k7electrical.com</li></ul>
  </div>
  <div class="footer-col" style="left:415px">
    <h4>Quick Links</h4>
    <ul><li>Home</li><li>About Us</li><li>Our Services</li></ul>
  </div>
  <div class="footer-col" style="left:703px">
    <h4>Resource</h4>
    <ul><li>Blog Post</li><li>FAQ</li><li>Contact Us</li></ul>
  </div>
  <div class="footer-col" style="left:950px">
    <h4>Social Media</h4>
    <div class="social"><i></i><i></i><i></i><i></i></div>
  </div>
</footer>
<div class="copyright">© Copyright 2018 K7 Electrical Services Ltd. All Rights Reserved &nbsp;|&nbsp; Privacy Policy.</div>

</body>
</html>
```